Simple Logo Design for Semi-Clear Plastic Frosted Card stock

Create a business card on frosted plastic. compliment existing logo elements with a tree trunk, roots, or seed at the lower half and the full logo both on the front.

Contact information will go on a solid portion of the back of this design since this card stock is semi-transparent.

It is important to consider this plastic card stock medium in your design. I found helpful tips and guides listed at vellaprint-sample.net: be careful to understand ink printed on plastic cards cannot have too much of a consistent print area or risks peeling and fine lines can easily scratch off.
Updates

2" x 3.5" 20PT Clear Plastic Business cards with Round corners Please get info or templates here: https://www.vellaprint-sample.net/product-detail/2-x-35-20pt-clear-plastic-business-cards-with-round-corners

Target Market(s)

Not for profit- religion

Industry/Entity Type

Business

Must include complementary elements to the existing logo

Font styles to use
Decorative

Colors
000000

Requirements
Must have
• Elements of community, nature and oneness. Such as: seed, roots, tree trunk, etc.
• Three lines of space on the back for Name, Title, Phone Number.
Nice to have
• I like a light use of decorative elements
Should not have
• No eyes, from faces or animals.

```html
<!DOCTYPE html>
<html lang="en">
<head>
<meta charset="utf-8">
<title>Rooted Path – Business Card</title>
<link href="https://fonts.googleapis.com/css2?family=Questrial&family=Crimson+Pro:wght@500&family=Arimo&display=swap" rel="stylesheet">
<style>
  :root {
    --page: #e8e8e5;
    --teal: #2f5a55;
    --teal-dark: #1e413d;
    --band-black: #161616;
    --band-green: #5f9a4f;
    --frost-light: #eeeeec;
    --frost-mid: #d9d9d6;
    --brand: #1f4e47;
    --name-green: #3f7d3a;
    --ink: #1a1a1a;
    --icon-green: #3f8a3a;
  }
  html, body {
    margin: 0;
    width: 1200px;
    height: 970px;
    overflow: hidden;
    background: var(--page);
  }
  .card {
    position: absolute;
    left: 50px;
    top: 155px;
    width: 1100px;
    height: 660px;
    border-radius: 30px;
    overflow: hidden;
    box-shadow: 0 10px 30px rgba(0,0,0,0.18);
  }
  .card-shapes {
    position: absolute;
    inset: 0;
  }
  .brand {
    position: absolute;
    left: 0;
    width: 1100px;
    top: 200px;
    display: flex;
    justify-content: center;
    align-items: center;
    gap: 22px;
    padding-left: 120px;
    box-sizing: border-box;
  }
  .brand-dot {
    width: 40px;
    height: 40px;
    border-radius: 50%;
    background: var(--brand);
  }
  .brand-name {
    font-family: "Questrial", sans-serif;
    font-size: 58px;
    letter-spacing: 2px;
    color: var(--brand);
    line-height: 1;
  }
  .holder-name {
    position: absolute;
    left: 159px;
    top: 352px;
    margin: 0;
    font-family: "Crimson Pro", serif;
    font-weight: 500;
    font-size: 48px;
    line-height: 1;
    color: var(--name-green);
  }
  .holder-title {
    position: absolute;
    left: 159px;
    top: 414px;
    margin: 0;
    font-family: "Arimo", sans-serif;
    font-size: 30px;
    line-height: 1;
    color: var(--ink);
  }
  .contact-list {
    position: absolute;
    right: 198px;
    top: 470px;
    margin: 0;
    padding: 0;
    list-style: none;
    font-family: "Arimo", sans-serif;
    font-size: 28px;
    color: var(--ink);
  }
  .contact-list li {
    display: flex;
    justify-content: flex-end;
    align-items: center;
    gap: 20px;
    height: 41px;
  }
  .contact-icon {
    width: 22px;
    height: 22px;
    flex: none;
  }
</style>
</head>
<body>
  <div class="card">
    <svg class="card-shapes" width="1100" height="660" viewBox="0 0 1100 660">
      <defs>
        <linearGradient id="frost" x1="0" y1="0" x2="1" y2="1">
          <stop offset="0" stop-color="var(--frost-light)"/>
          <stop offset="0.55" stop-color="var(--frost-mid)"/>
          <stop offset="1" stop-color="#e3e1df"/>
        </linearGradient>
        <linearGradient id="tealSide" x1="0" y1="0" x2="0" y2="1">
          <stop offset="0" stop-color="var(--teal)"/>
          <stop offset="1" stop-color="var(--teal-dark)"/>
        </linearGradient>
      </defs>
      <rect class="card-base" width="1100" height="660" fill="url(#tealSide)"/>
      <path class="band-black" d="M125 0 Q25 330 130 660 L960 660 Q1070 330 977 0 Z" fill="var(--band-black)"/>
      <path class="band-green" d="M158 0 Q62 330 145 660 L940 660 Q1040 330 945 0 Z" fill="var(--band-green)"/>
      <path class="frost-panel" d="M175 0 Q85 330 160 660 L920 660 Q1020 330 925 0 Z" fill="url(#frost)" role="img" aria-label="Frosted plastic panel with a faint damask pattern"/>
      <line class="divider" x1="452" y1="433" x2="971" y2="433" stroke="var(--ink)" stroke-width="2.5"/>
    </svg>

    <div class="brand">
      <span class="brand-dot"></span>
      <span class="brand-name">ROOTED PATH</span>
    </div>

    <h1 class="holder-name">Martin Hollowell</h1>
    <p class="holder-title">Managing Director</p>

    <ul class="contact-list">
      <li>0400 123 481
        <svg class="contact-icon" viewBox="0 0 22 22" aria-hidden="true"><rect width="22" height="22" rx="3" fill="var(--icon-green)"/><path d="M5 8 Q11 3 17 8 L15 10 L13 8 L9 8 L7 10 Z M6 12 H16 V17 H6 Z" fill="#fff"/></svg>
      </li>
      <li>0400 123 482
        <svg class="contact-icon" viewBox="0 0 22 22" aria-hidden="true"><rect width="22" height="22" rx="3" fill="var(--icon-green)"/><rect x="7" y="3" width="8" height="16" rx="1.5" fill="#fff"/><rect x="8.5" y="5" width="5" height="9" fill="var(--icon-green)"/></svg>
      </li>
      <li>martin@hollowell-sample.org
        <svg class="contact-icon" viewBox="0 0 22 22" aria-hidden="true"><rect width="22" height="22" rx="3" fill="var(--icon-green)"/><rect x="4" y="6" width="14" height="10" fill="#fff"/><path d="M4 6 L11 12 L18 6" fill="none" stroke="var(--icon-green)" stroke-width="1.5"/></svg>
      </li>
      <li>www.hollowell-sample.org
        <svg class="contact-icon" viewBox="0 0 22 22" aria-hidden="true"><rect width="22" height="22" rx="3" fill="var(--icon-green)"/><circle cx="11" cy="11" r="7" fill="none" stroke="#fff" stroke-width="1.6"/><path d="M4 11 H18 M11 4 Q6 11 11 18 M11 4 Q16 11 11 18" fill="none" stroke="#fff" stroke-width="1.3"/></svg>
      </li>
    </ul>
  </div>
</body>
</html>
```